KRL Stationery Design Project

Dear Designers,
We need a new stationery design for company to match our new logo.
Designers should provide a design for the following:
1. Business Card: 3.5x2 Inches.
2. Letterhead: A4 size.
3. Envelops: 25x35.5 Cm.
You can keep the Arabic name at the bottom of the logo Or you can use the separate attached Arabic Name.
Please refer to the attached logo guide for design information.
Sample Business Card information:
Name: Tarek Sowan
Position: Operation Manager
Tel: +966 920007164 Ex. 500
Fax: +966 (3)8842617
Mob: +966 (5)00263817
email: tarek@krl-example.com.sa
URL: www.krl-example.com.sa
Address:
Nakheel Heights, Suite 718
Zayed bin Omar Str.
Khobar, 31847
Saudi Arabia
Updates
Dear All,
Please note, we had uploaded our logo along with Arabic writing in Adobe illustrator format (.ai).
Regards,
Karim
Dear All,
A sample data for the business card had been added as per your request.
Regards,
Karim

```html
<!DOCTYPE html>
<html lang="en">
<head>
<meta charset="utf-8">
<title>KRL Business Card</title>
<link href="https://fonts.googleapis.com/css2?family=Open+Sans:wght@400;600;700&display=swap" rel="stylesheet">
<style>
  :root {
    --backdrop: #262728;
    --card: #ffffff;
    --navy: #0f2d52;
    --rule: #9ea3a8;
    --ink: #2b2b2b;
    --on-navy: #ffffff;
  }
  * { margin: 0; padding: 0; box-sizing: border-box; }
  html, body { width: 960px; height: 1200px; overflow: hidden; }
  body {
    background: var(--backdrop);
    font-family: "Open Sans", Arial, sans-serif;
    position: relative;
  }
  .card {
    position: absolute;
    background: var(--card);
    border-radius: 28px;
    overflow: hidden;
  }
  .card--front { left: 60px; top: 68px; width: 840px; height: 480px; }
  .card--back  { left: 57px; top: 625px; width: 840px; height: 478px; }

  .brand {
    position: absolute;
    left: 0; right: 0;
    display: flex;
    align-items: center;
    justify-content: center;
    gap: 22px;
    color: var(--navy);
    font-weight: 700;
    letter-spacing: 4px;
  }
  .brand__mark { background: var(--navy); }
  .card--front .brand { top: 95px; font-size: 92px; line-height: 1; }
  .card--front .brand__mark { width: 38px; height: 38px; }
  .card--back .brand { top: 160px; font-size: 120px; line-height: 1; }
  .card--back .brand__mark { width: 50px; height: 50px; }

  .band-rule {
    position: absolute; left: 0; right: 0; height: 2px;
    background: var(--rule);
  }
  .band-rule--top { top: 287px; }
  .band-rule--bottom { top: 387px; }
  .band {
    position: absolute; left: 0; right: 0; top: 294px; height: 90px;
    background: var(--navy);
    color: var(--on-navy);
  }
  .person { position: absolute; left: 140px; top: 14px; }
  .person__name { font-size: 26px; line-height: 34px; }
  .person__role { font-size: 20px; line-height: 28px; }
  .numbers { position: absolute; left: 536px; top: 18px; font-size: 20px; line-height: 30px; }

  .contact {
    position: absolute; left: 0; right: 0; top: 400px;
    text-align: center; color: var(--ink);
    font-size: 20px; line-height: 29px;
  }
  .contact b { font-style: italic; font-weight: 700; }
</style>
</head>
<body>
  <section class="card card--front">
    <div class="brand"><span class="brand__mark"></span><span class="brand__name">KRL</span></div>
    <div class="band-rule band-rule--top"></div>
    <div class="band">
      <div class="person">
        <p class="person__name">Your Name</p>
        <p class="person__role">Designation</p>
      </div>
      <div class="numbers">
        <p>t : 123-123-1234</p>
        <p>f : 123-123-1234</p>
      </div>
    </div>
    <div class="band-rule band-rule--bottom"></div>
    <div class="contact">
      <p><b>e</b> : info@krl-example.com.sa &nbsp;|&nbsp; <b>w</b> : www.krl-example.com.sa</p>
      <p>1234, Suite# 123, Street Name, State Name, Country Code</p>
    </div>
  </section>

  <section class="card card--back">
    <div class="brand"><span class="brand__mark"></span><span class="brand__name">KRL</span></div>
  </section>
</body>
</html>
```